Request for Business Card Design

Hi. My name is Marlene, I am looking for a new business card design for my company, Quarrow Signal Instruments, LLC. I really like the design you did for Tarsel Venture and was hoping you could do something similar using our full logo and our mark. I am also open to any raised texture design using our mark. I have attached our full logo, which would need to be somewhere on the card, as well as the mark in both outline and full form, as well as our brand colors / guide. The card does not have to be white, as long as our logo and mark appear. I actually like darker colored business cards more, but am open to all options. If you are interested in working with me, please let me know. We would also take the business card design into letterhead design if you can do that.

```html
<!DOCTYPE html>
<html lang="en">
<head>
<meta charset="utf-8">
<title>Quarrow Signal Instruments — Business Card</title>
<link rel="stylesheet" href="https://fonts.googleapis.com/css2?family=Barlow:wght@400;500;700&display=swap">
<style>
  :root {
    --backdrop: #7f97b8;
    --card-dark: #2b2829;
    --card-dark-hi: #3a3637;
    --brand-blue: #35a6cc;
    --brand-blue-deep: #2a96bf;
    --text-light: #f2f2f2;
    --text-muted: #c9c9c9;
    --mark-line: #bfe6f2;
  }
  * { box-sizing: border-box; margin: 0; padding: 0; }
  html, body { width: 1200px; height: 876px; overflow: hidden; }
  body {
    background: var(--backdrop);
    font-family: "Barlow", Arial, sans-serif;
    display: flex;
    align-items: center;
    justify-content: center;
    gap: 48px;
  }
  .card {
    position: relative;
    width: 520px;
    height: 297px;
    border-radius: 2px;
    box-shadow: 0 10px 24px rgba(40, 55, 85, 0.35);
    overflow: hidden;
  }

  /* Front */
  .card-front {
    background: linear-gradient(135deg, var(--card-dark) 0%, var(--card-dark-hi) 45%, var(--card-dark) 100%);
    border-top: 16px solid var(--brand-blue);
    border-bottom: 16px solid var(--brand-blue);
  }
  .contact-column {
    position: absolute;
    right: 258px;
    top: 42px;
    text-align: right;
  }
  .holder-name {
    color: var(--brand-blue);
    font-weight: 700;
    font-size: 17px;
    letter-spacing: 0.5px;
    text-transform: uppercase;
    line-height: 1;
  }
  .holder-role {
    color: var(--text-muted);
    font-size: 12px;
    margin-top: 3px;
  }
  .contact-list {
    list-style: none;
    margin-top: 34px;
  }
  .contact-list li {
    display: flex;
    align-items: center;
    justify-content: flex-end;
    gap: 8px;
    color: var(--text-light);
    font-size: 12.5px;
    line-height: 1;
    margin-bottom: 10px;
  }
  .contact-icon {
    width: 15px;
    height: 15px;
    flex: none;
  }
  .address-block { text-align: right; line-height: 1.3; }

  .brand-lockup {
    position: absolute;
    left: 282px;
    top: 128px;
    display: flex;
    align-items: center;
    gap: 10px;
  }
  .brand-dot {
    width: 26px;
    height: 26px;
    border-radius: 50%;
    background: var(--text-light);
    flex: none;
  }
  .brand-name {
    color: var(--text-light);
    font-weight: 700;
    font-size: 15px;
    line-height: 1.15;
    letter-spacing: 0.4px;
    text-transform: uppercase;
    width: 170px;
  }

  /* Back */
  .card-back {
    background: linear-gradient(150deg, #4fb8da 0%, var(--brand-blue) 45%, var(--brand-blue-deep) 100%);
    display: flex;
    flex-direction: column;
    align-items: center;
    justify-content: center;
    gap: 16px;
  }
  .back-circle {
    width: 118px;
    height: 118px;
    border-radius: 50%;
    border: 2px solid var(--mark-line);
  }
  .back-name {
    color: var(--mark-line);
    font-weight: 500;
    font-size: 15px;
    letter-spacing: 2px;
    text-transform: uppercase;
  }
</style>
</head>
<body>
  <section class="card card-front" aria-label="Business card front">
    <div class="contact-column">
      <p class="holder-name">Marlene</p>
      <p class="holder-role">Director</p>
      <ul class="contact-list">
        <li>+000 48213 5076
          <svg class="contact-icon" viewBox="0 0 16 16" aria-hidden="true"><circle cx="8" cy="8" r="8" fill="var(--brand-blue)"/><rect x="5.5" y="3.5" width="5" height="9" rx="1" fill="none" stroke="#fff" stroke-width="1.2"/></svg>
        </li>
        <li>marlene@quarrowsignal.com
          <svg class="contact-icon" viewBox="0 0 16 16" aria-hidden="true"><circle cx="8" cy="8" r="8" fill="var(--brand-blue)"/><rect x="4" y="5" width="8" height="6" fill="none" stroke="#fff" stroke-width="1.1"/><path d="M4 5l4 3.5L12 5" fill="none" stroke="#fff" stroke-width="1.1"/></svg>
        </li>
        <li><span class="address-block">Street Address Here<br>Larkmoor, 4410</span>
          <svg class="contact-icon" viewBox="0 0 16 16" aria-hidden="true"><circle cx="8" cy="8" r="8" fill="var(--brand-blue)"/><path d="M8 12.5s-3-3.2-3-5.5a3 3 0 0 1 6 0c0 2.3-3 5.5-3 5.5z" fill="#fff"/><circle cx="8" cy="7" r="1.1" fill="var(--brand-blue)"/></svg>
        </li>
      </ul>
    </div>
    <div class="brand-lockup">
      <span class="brand-dot" aria-hidden="true"></span>
      <span class="brand-name">Quarrow Signal Instruments</span>
    </div>
  </section>

  <section class="card card-back" aria-label="Business card back">
    <span class="back-circle" aria-hidden="true"></span>
    <span class="back-name">Quarrow Signal Instruments</span>
  </section>
</body>
</html>
```